Hoist Ridge Crane Sales Flyer

I need a professional modern flyer offering our crane services with our phone number and website. The flyer should focus on the blue crane and the red crane (KnuckleBooms) but include a small picture of the other cranes as well to show variety. This flyer will be mailed and emailed to a variety of roofing companies, HVAC, pool and mechanical contractors as well as precast concrete companies to attempt to earn their business. 8.5x11 single sided

HoistRidgeCranes.example
555 417-2093 should be number on flyer

```html
<!DOCTYPE html>
<html lang="en">
<head>
<meta charset="UTF-8">
<title>Hoist Ridge Crane – Sales Flyer</title>
<link href="https://fonts.googleapis.com/css2?family=Archivo+Black&family=Montserrat:wght@400;500;600&display=swap" rel="stylesheet">
<style>
  :root {
    --page-bg: #d9d9d9;
    --flyer-bg: #222222;
    --green: #2dbd3c;
    --green-line: #27a234;
    --white: #ffffff;
    --text: #f2f2f2;
    --photo-border: #f4f4f4;
  }
  * { margin: 0; padding: 0; box-sizing: border-box; }
  html, body { width: 670px; height: 1200px; overflow: hidden; }
  body { background: var(--page-bg); font-family: "Montserrat", sans-serif; position: relative; }

  .flyer {
    position: absolute; left: 10px; top: 180px;
    width: 650px; height: 841px;
    background: var(--flyer-bg);
    box-shadow: 0 10px 30px rgba(0,0,0,.35);
    color: var(--text);
  }
  .abs { position: absolute; }

  .brand { left: 36px; top: 82px; display: flex; align-items: center; gap: 10px; }
  .brand-mark { width: 16px; height: 16px; background: var(--green); }
  .brand-name { font-family: "Montserrat", sans-serif; font-weight: 600; font-size: 22px; color: var(--white); }

  .divider { left: 289px; top: 44px; width: 3px; height: 108px; background: var(--green); }

  .headline { left: 308px; top: 36px; font-family: "Archivo Black", sans-serif; line-height: 1.05; letter-spacing: -0.5px; }
  .headline .accent { color: var(--green); font-size: 33px; display: block; }
  .headline .main { color: var(--white); font-size: 29px; display: block; }
  .intro { left: 309px; top: 112px; width: 320px; font-size: 12px; line-height: 1.15; color: var(--text); }

  .trust { left: 27px; top: 184px; font-family: "Archivo Black", sans-serif; font-size: 24px; line-height: 1.02; color: var(--white); letter-spacing: -0.5px; }

  .photo { border: 3px solid var(--photo-border); }
  .photo-red { left: 289px; top: 169px; width: 337px; height: 189px; background: linear-gradient(160deg, #c9d7e6 0%, #a88a6a 55%, #4f5a3a 100%); }
  .photo-blue { left: 26px; top: 281px; width: 336px; height: 189px; background: linear-gradient(170deg, #2e7fe0 0%, #6aa3e8 45%, #333a48 100%); }
  .team-copy { left: 378px; top: 375px; width: 250px; font-size: 12px; line-height: 1.5; }

  .industries-title { left: 0; width: 670px; top: 493px; margin-left: -10px; text-align: center; font-family: "Archivo Black", sans-serif; font-size: 24px; color: var(--green); }

  .industries { left: 24px; top: 530px; width: 602px; height: 72px; display: flex; border: 1px solid var(--green-line); }
  .industry { border-right: 1px solid var(--green-line); padding: 16px 0 0 18px; font-size: 14px; font-weight: 500; line-height: 1.25; color: var(--white); }
  .industry:last-child { border-right: none; }

  .benefits { left: 24px; top: 614px; width: 320px; list-style: none; }
  .benefit { display: flex; gap: 7px; margin-bottom: 10px; }
  .benefit svg { flex: none; margin-top: 3px; }
  .benefit-title { font-size: 14px; font-weight: 600; color: var(--white); }
  .benefit-text { font-size: 14px; line-height: 1.25; color: var(--text); }

  .photo-mobile { left: 331px; top: 612px; width: 159px; height: 92px; background: linear-gradient(160deg, #7a8a6a 0%, #b4b6b0 60%, #8c8f8a 100%); }
  .photo-lift { left: 501px; top: 612px; width: 125px; height: 130px; background: linear-gradient(180deg, #2f78d8 0%, #6aa0e0 65%, #9aa3ad 100%); }
  .photo-yellow { left: 373px; top: 718px; width: 216px; height: 111px; background: linear-gradient(160deg, #1a3a78 0%, #5a4a2a 55%, #d19a22 100%); }

  .contact { left: 27px; top: 761px; width: 338px; height: 68px; background: var(--green); text-align: center; color: var(--white); }
  .phone { font-family: "Archivo Black", sans-serif; font-size: 37px; line-height: 1; margin-top: 3px; letter-spacing: -0.5px; }
  .website { font-size: 17px; font-weight: 500; margin-top: 2px; }
</style>
</head>
<body>
  <main class="flyer">
    <div class="abs brand">
      <span class="brand-mark"></span>
      <span class="brand-name">Hoist Ridge Crane</span>
    </div>

    <div class="abs divider"></div>
    <h1 class="abs headline">
      <span class="accent">CRANE SERVICE,</span>
      <span class="main">DONE AS PROMISED</span>
    </h1>
    <p class="abs intro">Crane service partners that meet deadlines, prioritize safety, and stay within budget with end-to-end support.</p>

    <h2 class="abs trust">TRUSTED CRANE<br>COMPANY IN OH.<br>&amp; IN.</h2>

    <div class="abs photo photo-red" role="img" aria-label="Red knuckle boom crane lifting to a brick building rooftop"></div>
    <div class="abs photo photo-blue" role="img" aria-label="Blue knuckle boom crane truck parked beside a commercial building"></div>

    <p class="abs team-copy">Our team of project planners and operators is committed to serving your project’s needs every step of the way, ensuring safety and done right the first time without major disruptions.</p>

    <h2 class="abs industries-title">INDUSTRIES WE SERVE</h2>
    <div class="abs industries">
      <div class="industry" style="width:116px">Tree and<br>Landscape</div>
      <div class="industry" style="width:138px;padding-left:24px">Steel<br>Construction</div>
      <div class="industry" style="width:87px">HVAC<br>lifts</div>
      <div class="industry" style="width:133px">General<br>Construction</div>
      <div class="industry" style="width:128px">Container<br>Lifts</div>
    </div>

    <ul class="abs benefits">
      <li class="benefit">
        <svg width="14" height="12" viewBox="0 0 14 12"><path d="M1 6.5 L5 10.5 L13 1.5" fill="none" stroke="#2dbd3c" stroke-width="2"/></svg>
        <div><div class="benefit-title">Fastest Workflow</div><div class="benefit-text">Our well-maintained cranes &amp; skilled operators deliver a smooth experience.</div></div>
      </li>
      <li class="benefit">
        <svg width="14" height="12" viewBox="0 0 14 12"><path d="M1 6.5 L5 10.5 L13 1.5" fill="none" stroke="#2dbd3c" stroke-width="2"/></svg>
        <div><div class="benefit-title">Budget Friendly</div><div class="benefit-text">We send the right size crane to get the job done safely, so you don’t overpay for what you don’t use.</div></div>
      </li>
    </ul>

    <div class="abs photo photo-mobile" role="img" aria-label="White mobile crane set up in a parking lot"></div>
    <div class="abs photo photo-lift" role="img" aria-label="Crane lifting a helicopter onto a rooftop against blue sky"></div>
    <div class="abs photo photo-yellow" role="img" aria-label="Yellow all-terrain crane working at night under a steel structure"></div>

    <div class="abs contact">
      <div class="phone">555 417-2093</div>
      <div class="website">Visit us at - HoistRidgeCranes.example</div>
    </div>
  </main>
</body>
</html>
```